B2B Tear Sheet / Flyer for Corvath Summit Partners

Design multiple creative treatments for a 1-page, 2-sided tear sheet/flyer for a B2B consulting firm called Corvath Summit Partners, targeting Private Equity firms, Family Offices, Investment Banks, and Independent Sponsors. This piece will be handed out at conferences, 1-on-1 meetings, and potential snail mail (direct mail) campaigns. Eventually, the piece could also be made available on our website. The company is in start-up mode, so our website is not yet up and working. But we do have a logo and color palette.

```html
<!DOCTYPE html>
<html lang="en">
<head>
<meta charset="utf-8">
<title>Corvath Summit Partners – Tear Sheet</title>
<link href="https://fonts.googleapis.com/css2?family=Montserrat:wght@400;500;600;700;800&display=swap" rel="stylesheet">
<style>
:root{
  --backdrop:#8fab9a;
  --green:#3d5a48;
  --green-dark:#334d3d;
  --paper:#f7f8f9;
  --paper-shade:#eceef1;
  --ink:#3b3f44;
  --muted:#6a7078;
  --rule:#c9ced3;
}
*{box-sizing:border-box;margin:0;padding:0}
html,body{width:1200px;height:1200px;overflow:hidden}
body{background:var(--backdrop);font-family:"Montserrat",sans-serif;color:var(--ink);position:relative}
.sheet{position:absolute;top:210px;width:560px;height:780px;background:var(--paper);overflow:hidden;box-shadow:0 14px 30px rgba(30,50,40,.25);display:flex;flex-direction:column}
.sheet--front{left:30px}
.sheet--back{left:610px}

/* front */
.masthead{background:var(--green);height:42px;display:flex;align-items:center;justify-content:center;gap:8px}
.brand-dot{width:12px;height:12px;border:2px solid #fff;flex:none}
.brand-name{color:#fff;font-weight:600;font-size:15px;letter-spacing:.5px}
.hero-photo{height:112px;margin:0 10px;background:linear-gradient(180deg,#dfe6ee,#b9c4d2 60%,#5c6a80)}
.title-band{background:var(--green);color:#fff;text-align:center;font-weight:800;font-size:13px;line-height:1.3;padding:10px 20px;text-transform:uppercase}
.intro{padding:9px 22px 8px;text-align:center}
.intro h2{font-size:11px;font-weight:700;color:var(--green)}
.intro h2 span{font-weight:400}
.intro p{font-size:6.2px;line-height:1.5;margin-top:4px;color:var(--muted)}
.band{background:var(--green);color:#fff;text-align:center;font-weight:800;font-size:9px;padding:4px;text-transform:uppercase;letter-spacing:.3px}
.cols{display:grid;grid-template-columns:1fr 1fr;padding:6px 0}
.cols>div{padding:0 22px}
.cols>div+div{border-left:1px solid var(--rule)}
.col-title{font-size:8.5px;font-weight:700;color:var(--green)}
.col-sub{font-size:7px;font-weight:600;margin-bottom:2px}
.list{list-style:none}
.list li{font-size:6.6px;line-height:1.55;padding-left:9px;position:relative}
.list li::before{content:"";position:absolute;left:0;top:3px;width:4px;height:4px;background:var(--green)}
.plain li{font-size:6.8px;line-height:1.6}
.note{display:inline-block;background:var(--green);color:#fff;font-size:6px;padding:2px 6px;margin-top:3px}
.gains-title{text-align:center;font-weight:700;color:var(--green);font-size:10px;padding:6px 0 4px}
.gains{display:grid;grid-template-columns:repeat(3,1fr);padding:2px 0 10px;flex:1}
.gains>div{padding:0 14px;display:flex;flex-direction:column;gap:5px;align-items:center}
.gains>div+div{border-left:1px solid var(--rule)}
.pill{background:var(--green);color:#fff;font-size:5.8px;line-height:1.35;text-align:center;padding:4px 6px;width:100%}

/* back */
.back-head{background:var(--green);color:#fff;text-align:center;font-weight:800;font-size:17px;padding:18px 0 14px;text-transform:uppercase}
.reasons{padding:12px 22px 8px}
.reasons p{font-size:7.4px;line-height:1.6;text-align:justify;margin-bottom:7px}
.founder{display:grid;grid-template-columns:1fr 180px;gap:14px;padding:8px 22px 10px;align-items:start}
.founder p{font-size:7.4px;line-height:1.65;text-align:justify}
.founder-photo{height:150px;border:5px solid var(--green);background:linear-gradient(160deg,#e8ecef,#b8c3cc 55%,#7d95ad)}
.creds{list-style:none;padding:12px 22px 12px;flex:1;display:flex;flex-direction:column;justify-content:space-evenly}
.creds li{font-size:8.6px;line-height:1.5;padding-left:12px;position:relative}
.creds li::before{content:"";position:absolute;left:0;top:4px;width:5px;height:5px;background:var(--green)}
.footer{background:var(--green);color:#fff;height:110px;display:flex;align-items:center;padding:0 24px;gap:20px;flex:none}
.footer-brand{display:flex;flex-direction:column;align-items:center;gap:6px;padding-right:20px;border-right:1px solid rgba(255,255,255,.5);height:64px;justify-content:center}
.footer-brand .brand-name{font-size:11px;text-align:center;width:110px}
.contact{font-size:10.5px;line-height:1.8}
.contact b{font-weight:700}
</style>
</head>
<body>

<article class="sheet sheet--front">
  <header class="masthead"><span class="brand-dot"></span><span class="brand-name">Corvath Summit Partners</span></header>
  <div class="hero-photo" role="img" aria-label="Photo of business professionals shaking hands across a bright office table"></div>
  <h1 class="title-band">Fractional Marketing Services for Private Equity<br>Funds, Family Offices &amp; Investment Banks</h1>
  <section class="intro">
    <h2>Fractional Marketing Services: <span>The Alternative to a Full-Time Marketing Staff</span></h2>
    <p>Hiring a full-time corporate marketing staff, or even a single marketing employee, can be an expensive proposition. Corvath Summit Partners provides Part-Time Marketing Services to middle market clients, which allow them to receive best-in-class corporate marketing at a fraction of the cost of a full-time Analyst or Associate, or even an entry-level Marketing Coordinator. Fractional Marketing Services have been used for years for Private Equity portfolio companies, but only recently have they been made available to Private Equity Funds themselves, Family Offices, and Investment Banks. When selecting a Fractional Marketing Services resource, prospective clients should ensure their Fractional Chief Marketing Officer (CMO) has broad firsthand Private Equity and Banking experience in the areas of Marketing, Business Development, Fundraising, and Principal Investing, along with 21st Century tools to increase lead generation, deal flow, and stakeholder satisfaction.</p>
  </section>
  <div class="band">Fractional Marketing Services</div>
  <section class="cols">
    <div>
      <h3 class="col-title">Monthly Retained Marketing Services</h3>
      <p class="col-sub">Strategy, Management &amp; Execution</p>
      <ul class="list">
        <li>Up to 20-Hours/Month</li><li>Press Release Drafting &amp; Distribution</li><li>Email Campaigns &amp; Drip Marketing / Lead Nurturing</li><li>Digital Marketing &amp; Advertising</li><li>Content Development &amp; Collateral Management</li><li>Website Analysis, Updates &amp; Remarketing</li><li>SEO &amp; SEM</li><li>Dashboard &amp; KPIs</li><li>Vendor Tool Selection &amp; Implementation</li><li>List Management</li><li>Go-to-Market Strategy</li><li>ProLink Enhancement &amp; Lead Gen</li><li>Other Social Media</li><li>Offline Activity Management</li>
      </ul>
    </div>
    <div>
      <h3 class="col-title">Marketing Audit &amp; Planning Services</h3>
      <p class="col-sub">Assessment Areas</p>
      <ul class="list">
        <li>Website &amp; Traffic Analysis</li><li>SEO &amp; SEM</li><li>Social Media (e.g., ProLink, etc.)</li><li>Email &amp; Other Digital</li><li>Press Releases</li><li>Collaterals</li><li>Content Management / CMS</li><li>ThinkBot and A.I.</li><li>Advertising (if applicable)—all channels</li><li>Full-Funnel Evaluation</li><li>Biz Dev &amp; Marketing Integration</li><li>CRM &amp; Data Integrity</li><li>Creative Assessment</li><li>Strategy, Messaging &amp; Marketing Plan (optional)</li>
      </ul>
    </div>
  </section>
  <div class="band">Special Project</div>
  <section class="cols">
    <div><ul class="list"><li>Branding &amp; Rebranding</li><li>Website Overhaul</li><li>Corporate Identity</li><li>Data Cleansing</li><li>Video Production &amp; Management</li></ul></div>
    <div><ul class="list"><li>CRM Selection, Design &amp; Transition</li><li>Customer Intelligence Studies</li><li>Marketing Brainstorming &amp; Facilitation</li><li>Marketing Resource Evaluation</li><li>Boards of Directors</li></ul></div>
  </section>
  <div class="band">Special Project</div>
  <section class="cols">
    <div>
      <ul class="plain list"><li>For Inaugural &amp; Follow-on Funds</li><li>6 &amp; 12-Month Projects</li><li>Limited Availability</li><li>Fees based on fund size, number, stage &amp; complexity</li></ul>
      <span class="note">New Fund Launch Services can commence before or during fundraising</span>
    </div>
    <div><ul class="list"><li>Includes all Fractional Marketing Services (above)</li><li>Plus: Website creation or overhaul</li><li>Plus: CRM design &amp; implementation</li><li>Plus: Corporate identity work</li><li>Plus: Social media &amp; digital launch</li><li>Plus: Marketing Audit for follow-on funds</li><li>Plus: Business development and GTM strategy</li></ul></div>
  </section>
  <h2 class="gains-title">With Corvath Summit Partners Fractional Marketing Services, you can:</h2>
  <section class="gains">
    <div><span class="pill">Receive Best-in-Class Marketing strategies &amp; tactics for a fraction of the cost of an Analyst</span><span class="pill">Leverage the experience of a 17+ year middle market Private Equity Chief Marketing Officer</span></div>
    <div><span class="pill">No benefits or payroll taxes</span><span class="pill">No need to stay knowledgeable on marketing and lead generation tactics, which change daily</span></div>
    <div><span class="pill">100% remote, with onsite work from time-to-time and at your discretion</span><span class="pill">Receive LP-friendly reports to prove your differentiation and ensure their satisfaction</span></div>
  </section>
</article>

<article class="sheet sheet--back">
  <h1 class="back-head">Our Reasons for Being</h1>
  <section class="reasons">
    <p>Today's increasingly competitive environment for middle market Private Equity Funds, Family Offices, and Investment Banks, has left little time for those entities to focus on their marketing strategies, tactics, and execution. At best, a Business Development executive is forced to take on a Marketing role as a part-time, almost side job, taking valuable time away from their in-person deal origination responsibilities. At worst, a GP whose primary focus is on deal evaluation and execution, is forced to give up hours of their time trying to perform tasks in which they are not trained or updated in 21st Century marketing tactics. Marketing goes beyond Business Development but should work with it in an integrated manner to ensure a seamless connection between funds and their three primary target markets: Investors, Private Company Owners, and Deal Sources.</p>
    <p>Corvath Summit Partners was created to bring Fractional Marketing Services to Private Equity Funds and Family Offices and the Intermediaries and Counselors who serve them. For years, the Fractional Marketing Services concept has been leveraged in Private Equity, but only for Portfolio Companies, with little Corporate Marketing attention given to the funds themselves. Finally, Private Equity Funds, Family Offices, and Investment Banks are realizing they are too busy competing to win the next deal and enhancing Portco equity value to be able to focus on a Marketing and Lead Generation system that is dynamic and ever-changing. At Corvath Summit Partners, we believe that roughly 1/3 of the skills required to be a successful B2B financial services marketer today have not even been identified yet. Why not leave the execution of your critical marketing function to a firm that breathes Private Equity, Family Office, and Investment Bank Marketing full-time? Contact us immediately for a no obligation discussion at 1.555.210.4870 or DanielR@CorvathSummit.com.</p>
  </section>
  <div class="band">Principal &amp; Founder</div>
  <section class="founder">
    <p>With 25 years of Private Equity experience, 17 of which as Chief Marketing Officer (CMO) for middle market funds, past General Partner, his knowledge of Private Equity development, fundraising, principal investing, and management, positions him unlike any other in the industry. With an Investor's Mindset, Daniel has experience in buyouts, mezzanine, growth equity, ABL, and venture. Unlike agency experienced marketers who lack the empathy, Corvath Summit Partners has firsthand knowledge of what GPs must accomplish to satisfy their three primary target markets: Investors, Owners, and Deal Sources.</p>
    <div class="founder-photo" role="img" aria-label="Portrait of the founder smiling at his desk beside a computer"></div>
  </section>
  <div class="band">“A Marketer with an Investor's Mindset”</div>
  <ul class="creds">
    <li>17-Years as Private Equity Chief Marketing Officer—one of the industry's first</li>
    <li>25-Years total Private Equity experience, including Marketing, Business Development, Fundraising &amp; Principal Investing</li>
    <li>40-Years total Sales and Marketing experience, including Corporate and Global Strategy Consulting</li>
    <li>Experienced in most asset classes, including Buyouts, Growth Equity, Mezzanine, ABL and Venture</li>
    <li>More deal, business development, and marketing experienced than any Analyst or Associate, typically assigned to these roles</li>
    <li>Arguably, the most experienced middle market Private Equity marketer in the U.S.</li>
  </ul>
  <footer class="footer">
    <div class="footer-brand"><span class="brand-dot"></span><span class="brand-name">Corvath Summit Partners</span></div>
    <div class="contact">
      <div><b>Cell:</b> 1.555.210.4870 &nbsp;|&nbsp; <b>Mail:</b> danielr@corvathsummit.com</div>
      <div><b>Web:</b> www.corvathsummit.com</div>
    </div>
  </footer>
</article>

</body>
</html>
```